High-end law practice specializing in closely held business succession planning and complex estates

Solo practitioner whose practice specializes in high-net worth, complex estate planning needs muliple versions of letterhead black and white, please. Letterhead should incorporate slogan, "Protecting your family business is my business," for one and "Complex Estate Planning"; third with no slogan. All for The Law Office of Marcy Lynn Pettibone, PC, 418 Cedar Hollow Ln., Newport News, Virginia 23648, Tel. 757-555-0142 Fax tbd email: marcy@mlplawgroup.example; Marcy Lynn Pettibone, Esq., principal, licensed in VA, NY, DC
Updates

Project Deadline Extended
Reason: My internet service went down and I can only view designs on my smart phone -- it's just too hard to review. So sorry! Working with my ISP now. Please be patient!

Target Market(s)

High net worth clients with complex estate planning needs, family businesses, family farmers, family foresters -- people with unique estate/succession planning needs who need a specialist who understands them.

Industry/Entity Type

Business

Font styles to use
Script

Requirements
Must have
• A high-end look and feel, connoting trustworthiness, special knowledge, and expertise.

```html
<!DOCTYPE html>
<html lang="en">
<head>
<meta charset="utf-8">
<title>Letterhead – The Law Office of Marcy Lynn Pettibone, PC</title>
<link rel="stylesheet" href="https://fonts.googleapis.com/css2?family=Libre+Bodoni:wght@700&family=Zilla+Slab:wght@300;400&display=swap">
<style>
  :root {
    --ink: #2f2f31;
    --paper: #ffffff;
    --edge: #8a8a8a;
    --icon-tone: #d9d9db;
    --band: #333335;
    --on-band: #ffffff;
  }
  * { margin: 0; padding: 0; box-sizing: border-box; }
  html, body { width: 848px; height: 1200px; overflow: hidden; background: var(--paper); }
  .sheet {
    position: relative;
    width: 848px;
    height: 1200px;
    background: var(--paper);
    border: 1px solid var(--edge);
    overflow: hidden;
    font-family: "Zilla Slab", Georgia, serif;
    color: var(--ink);
  }
  .monogram {
    position: absolute;
    left: 36px;
    top: 66px;
    width: 100px;
    height: 100px;
    border: 3px solid var(--ink);
    border-radius: 50%;
    display: flex;
    align-items: center;
    justify-content: center;
    font-family: "Libre Bodoni", Georgia, serif;
    font-weight: 700;
    font-size: 34px;
    letter-spacing: -1px;
    color: var(--ink);
  }
  .firm {
    position: absolute;
    left: 171px;
    top: 62px;
  }
  .firm-prefix {
    font-weight: 300;
    font-size: 25px;
    line-height: 30px;
  }
  .firm-name {
    font-family: "Libre Bodoni", Georgia, serif;
    font-weight: 700;
    font-size: 23px;
    line-height: 28px;
  }
  .slogan {
    margin-top: 5px;
    font-weight: 300;
    font-size: 17px;
    line-height: 21px;
  }
  .practice-icons {
    position: absolute;
    left: 465px;
    top: 68px;
    width: 353px;
    height: 38px;
  }
  .credentials {
    position: absolute;
    left: 459px;
    top: 123px;
    width: 389px;
    height: 23px;
    background: var(--band);
    color: var(--on-band);
    font-weight: 400;
    font-size: 18px;
    line-height: 23px;
    padding-left: 11px;
  }
  .footer-band {
    position: absolute;
    left: 0;
    bottom: 0;
    width: 848px;
    height: 160px;
  }
  .contact {
    position: absolute;
    left: 0;
    width: 848px;
    text-align: center;
    color: var(--on-band);
    font-weight: 400;
    font-size: 14px;
    line-height: 18px;
  }
  .contact-address { top: 1137px; }
  .contact-lines { top: 1162px; font-size: 13.5px; }
  .sep { padding: 0 5px; }
</style>
</head>
<body>
  <div class="sheet">
    <header>
      <div class="monogram">MLP</div>
      <div class="firm">
        <div class="firm-prefix">The Law Office of</div>
        <div class="firm-name">Marcy Lynn Pettibone, PC</div>
        <p class="slogan">Protecting your family<br>business is my business.</p>
      </div>
      <svg class="practice-icons" viewBox="0 0 353 38" role="img" aria-label="Row of practice-area icons: oath, justice, gavel, scales, finance, family, passport, handshake">
        <rect x="0" y="0" width="353" height="38" fill="var(--icon-tone)"/>
      </svg>
      <div class="credentials">Esq., principal, licensed in VA, NY, DC</div>
    </header>

    <footer>
      <svg class="footer-band" viewBox="0 0 848 160" preserveAspectRatio="none" aria-hidden="true">
        <path d="M0 44 C 300 60, 640 40, 848 0 L 848 160 L 0 160 Z" fill="var(--band)"/>
      </svg>
      <p class="contact contact-address">Address: 418 Cedar Hollow Ln., Newport News, Virginia 23648,</p>
      <p class="contact contact-lines">Telephone: 757-555-0142<span class="sep">|</span>Fax: 757-555-0199<span class="sep">|</span>E-mail: marcy@mlplawgroup.example<span class="sep">|</span>Website: www.mlplawgroup.example</p>
    </footer>
  </div>
</body>
</html>
```